Alaska Law Firm Needs a Sticker Design

We need a design for stickers to put on already-printed brochures. We mail the brochures to potential clients so they can learn more about accident-induced injuries, insurance claims, legal representation, and our own law firm.

One of our lawyers wrote a book that provides a helpful overview of personal injury claims. We are offering this book for free to anyone who calls and requests it. Therefore, the sticker design should include one of the following phrases, or something very similar:
a) "Still have questions? Call and request our book-- for free!"
b) "Still have questions about auto accident claims? Call and request our book today."
c) "Still have questions about filing a claim? Call and request a free copy of our book."
d) "Still have questions? Call us today to request a free copy of our book, Clear Lanes Ahead."
e) "To learn more about automobile accidents and insurance, call today and request a free copy of our book."

The sticker should be approximately 3"x3" and may be a circle, square, rectangle, or ellipsis. The sticker will be placed on the back of the folder, which is light blue. We would like the sticker to match the color scheme of our website and the folder.

I will upload an image of the book cover as soon as I obtain it.

Law Firm

Font styles to use
Serif
Sans Serif

Requirements
Should not have
• Bright colors that aren't already used in the folder design. e.g. no bright orange, pink, chartreuse, turquoise, yellow, red.

```html
<!DOCTYPE html>
<html lang="en">
<head>
<meta charset="utf-8">
<title>Clear Lanes Ahead – Free Book Sticker</title>
<link rel="stylesheet" href="https://fonts.googleapis.com/css2?family=Bebas+Neue&family=Montserrat:wght@600&family=Open+Sans:wght@400;800&display=swap">
<style>
  :root {
    --navy: #143f66;
    --navy-deep: #15174a;
    --sky: #d8e6f7;
    --white: #ffffff;
    --backdrop: #ececec;
    --ink: #111111;
    --photo-top: #b9d3a0;
    --photo-bottom: #6f9a4c;
  }
  html, body {
    margin: 0;
    padding: 0;
    width: 1200px;
    height: 1085px;
    overflow: hidden;
    background: var(--backdrop);
  }
  .canvas {
    position: relative;
    width: 1200px;
    height: 1085px;
  }
  .sticker {
    position: absolute;
    left: 145px;
    top: 87px;
    width: 910px;
    height: 910px;
    border-radius: 50%;
    background: var(--white);
  }
  .sticker-face {
    position: absolute;
    left: 16px;
    top: 16px;
    width: 878px;
    height: 878px;
    border-radius: 50%;
    background: var(--sky);
    overflow: hidden;
  }
  .headline {
    position: absolute;
    left: 0;
    width: 100%;
    text-align: center;
    font-family: "Bebas Neue", sans-serif;
    color: var(--navy);
    margin: 0;
    line-height: 1;
  }
  .headline-main {
    top: 76px;
    font-size: 128px;
    letter-spacing: 1px;
  }
  .headline-sub {
    top: 178px;
    font-size: 84px;
    letter-spacing: 21px;
    padding-left: 21px;
    box-sizing: border-box;
    color: var(--white);
    -webkit-text-stroke: 3px var(--navy);
  }
  .book-ghost {
    position: absolute;
    top: 312px;
    width: 120px;
    height: 235px;
    background: linear-gradient(var(--white) 0 18%, var(--photo-top) 18% 80%, var(--navy-deep) 80%);
    filter: blur(5px);
    opacity: 0.85;
  }
  .book-ghost.left { left: 265px; }
  .book-ghost.right { left: 493px; }
  .book-cover {
    position: absolute;
    left: 336px;
    top: 266px;
    width: 210px;
    height: 328px;
    background: var(--white);
    box-shadow: 0 2px 6px rgba(0,0,0,0.2);
    display: flex;
    flex-direction: column;
    align-items: center;
  }
  .book-author {
    margin-top: 14px;
    font-family: "Open Sans", sans-serif;
    font-size: 11px;
    color: var(--ink);
    letter-spacing: 0.3px;
  }
  .book-title {
    margin: 6px 0 0;
    font-family: "Open Sans", sans-serif;
    font-weight: 800;
    font-size: 22px;
    line-height: 1.05;
    color: var(--navy-deep);
    text-align: center;
  }
  .book-photo {
    margin-top: 8px;
    width: 194px;
    height: 175px;
    background: linear-gradient(var(--photo-top), var(--photo-bottom));
  }
  .book-subtitle {
    width: 194px;
    height: 38px;
    margin-top: 0;
    background: var(--navy-deep);
    color: var(--white);
    font-family: "Open Sans", sans-serif;
    font-size: 9.5px;
    line-height: 1.3;
    text-align: center;
    display: flex;
    align-items: center;
    justify-content: center;
  }
  .offer-band {
    position: absolute;
    left: 0;
    top: 596px;
    width: 100%;
    height: 196px;
    background: var(--navy);
    text-align: center;
    color: var(--white);
    font-family: "Bebas Neue", sans-serif;
  }
  .offer-call {
    margin: 0;
    padding-top: 18px;
    font-size: 50px;
    line-height: 1;
    letter-spacing: 0.5px;
  }
  .offer-free {
    margin: 0;
    padding-top: 8px;
    font-size: 124px;
    line-height: 1;
    letter-spacing: 1px;
  }
  .phone {
    position: absolute;
    left: 0;
    top: 806px;
    width: 100%;
    margin: 0;
    text-align: center;
    font-family: "Montserrat", sans-serif;
    font-weight: 600;
    font-size: 38px;
    color: var(--ink);
  }
</style>
</head>
<body>
<main class="canvas">
  <section class="sticker">
    <div class="sticker-face">
      <h1 class="headline headline-main">Still Have</h1>
      <h2 class="headline headline-sub">Questions?</h2>

      <div class="book-ghost left" aria-hidden="true"></div>
      <div class="book-ghost right" aria-hidden="true"></div>

      <div class="book-cover">
        <span class="book-author">DANIEL R. HOLLIS</span>
        <p class="book-title">CLEAR LANES<br>AHEAD</p>
        <div class="book-photo" role="img" aria-label="Cover photo of a smiling family lying on grass beside a small red car"></div>
        <div class="book-subtitle">THE RIGHT WAY TO HANDLE<br>YOUR AUTO ACCIDENT CLAIM</div>
      </div>

      <div class="offer-band">
        <p class="offer-call">Call &amp; Request Our Book</p>
        <p class="offer-free">For Free !!</p>
      </div>

      <p class="phone">(907) 555-0148</p>
    </div>
  </section>
</main>
</body>
</html>
```